Property maintenance company needs an eye catching postcard design

We are a property maintenance company that wants to send out a postcard targeting residential homeowners only. We want the postcard to create the impression of a friendly and inviting company that makes maintenance easy for homeowners. I have attached all the instructions in a pdf file as well as any other needed pictures or info. Please read the outline I provided. I also attached pictures/screenshots of our new (in progress) website if you wish to get a feel for our company.

Thanks!

Target Market(s)

residential homeowners, homeowners

Industry/Entity Type

Property Maintenance

```html
<!DOCTYPE html>
<html lang="en">
<head>
<meta charset="UTF-8">
<title>Hearthline Postcard</title>
<link rel="stylesheet" href="https://fonts.googleapis.com/css2?family=Montserrat:wght@400;500;600;700;800&display=swap">
<style>
  :root {
    --bg: #e8e8e6;
    --card: #f6f6f6;
    --blue: #3d4fa3;
    --blue-light: #6b87c9;
    --green: #8cc74a;
    --ink: #2b2b2b;
    --photo-warm-a: #8a5a4a;
    --photo-warm-b: #b9c7c4;
    --photo-cool-a: #e9ecef;
    --photo-cool-b: #5a6fa8;
  }
  * { box-sizing: border-box; margin: 0; padding: 0; }
  html, body { width: 1200px; height: 900px; overflow: hidden; }
  body {
    background: var(--bg);
    font-family: "Montserrat", sans-serif;
    color: var(--ink);
    position: relative;
  }
  .postcard {
    position: absolute;
    left: 290px;
    width: 620px;
    height: 410px;
    background: var(--card);
    box-shadow: 0 3px 10px rgba(0,0,0,0.18);
    overflow: hidden;
  }
  .postcard--back { top: 22px; }
  .postcard--front { top: 466px; }
  .postcard svg.shapes { position: absolute; inset: 0; }

  /* front text */
  .brand {
    position: absolute;
    left: 34px;
    top: 58px;
    display: flex;
    align-items: center;
    gap: 10px;
    font-size: 27px;
    font-weight: 500;
    letter-spacing: 0.5px;
    color: var(--blue);
  }
  .brand-square {
    width: 20px; height: 20px;
    background: var(--blue);
  }
  .headline {
    position: absolute;
    left: 31px;
    top: 124px;
    font-size: 27px;
    line-height: 36px;
    text-transform: uppercase;
  }
  .headline .accent-blue { color: var(--blue-light); font-weight: 800; }
  .headline .accent-green { color: var(--green); font-weight: 800; }
  .headline .plain { font-weight: 400; color: var(--ink); }
  .headline-rule {
    position: absolute;
    left: 31px; top: 269px;
    width: 154px; height: 2px;
    background: var(--blue);
  }
  .tagline {
    position: absolute;
    left: 31px; top: 279px;
    font-size: 11.5px;
    font-weight: 500;
    line-height: 14px;
    text-transform: uppercase;
  }
  .services {
    position: absolute;
    left: 31px; top: 322px;
    display: grid;
    grid-template-columns: 120px 130px;
    row-gap: 8px;
  }
  .service {
    display: flex; align-items: center; gap: 8px;
    font-size: 10.5px; font-weight: 500; line-height: 13px;
    text-transform: uppercase;
  }
  .service svg { flex: none; }
</style>
</head>
<body>

<section class="postcard postcard--back" aria-label="Postcard address side">
  <svg class="shapes" width="620" height="410" viewBox="0 0 620 410">
    <defs>
      <linearGradient id="backPhoto" x1="0" y1="0" x2="1" y2="1">
        <stop offset="0" stop-color="var(--photo-warm-b)"/>
        <stop offset="0.55" stop-color="var(--photo-warm-a)"/>
        <stop offset="1" stop-color="#5a3a36"/>
      </linearGradient>
    </defs>
    <polygon points="0,0 331,0 298,410 0,410" fill="url(#backPhoto)" role="img" aria-label="Photo of a plumber inspecting a chrome sink pipe"/>
    <polygon points="350,0 371,0 325,410 304,410" fill="var(--blue)"/>
    <rect x="474" y="36" width="102" height="103" fill="none" stroke="var(--blue)" stroke-width="1"/>
    <g stroke="var(--blue)" stroke-width="1">
      <line x1="385" y1="166" x2="576" y2="166"/>
      <line x1="385" y1="193" x2="576" y2="193"/>
      <line x1="385" y1="221" x2="576" y2="221"/>
      <line x1="385" y1="248" x2="576" y2="248"/>
    </g>
  </svg>
</section>

<section class="postcard postcard--front" aria-label="Postcard front">
  <svg class="shapes" width="620" height="410" viewBox="0 0 620 410">
    <defs>
      <linearGradient id="frontPhoto" x1="0" y1="0" x2="0" y2="1">
        <stop offset="0" stop-color="var(--photo-cool-a)"/>
        <stop offset="0.45" stop-color="var(--photo-cool-b)"/>
        <stop offset="1" stop-color="#dfe2e6"/>
      </linearGradient>
    </defs>
    <polygon points="292,0 620,0 620,410 322,410" fill="url(#frontPhoto)" role="img" aria-label="Photo of a plumber kneeling at a kitchen cabinet with pipe fittings on the floor"/>
    <polygon points="246,0 259,0 319,410 309,410" fill="var(--blue)"/>
  </svg>

  <div class="brand"><span class="brand-square"></span>HEARTHLINE</div>

  <h1 class="headline">
    <span class="accent-blue">Hearthline</span><br>
    <span class="plain">Makes </span><span class="accent-green">Home</span><br>
    <span class="accent-green">Maintenance</span><br>
    <span class="plain">Easy</span>
  </h1>
  <div class="headline-rule"></div>
  <p class="tagline">One point of contact for all your<br>property maintenance needs</p>

  <div class="services">
    <div class="service">
      <svg width="32" height="32" viewBox="0 0 32 32" fill="none" stroke="var(--blue)" stroke-width="1.2">
        <circle cx="16" cy="16" r="15"/>
        <path d="M9 17c0-5 4-8 8-8s6 3 5 5-4 1-4 3 3 2 1 4-10 2-10-4z"/>
        <circle cx="13" cy="14" r="1"/><circle cx="17" cy="12" r="1"/>
      </svg>
      Painting
    </div>
    <div class="service">
      <svg width="32" height="32" viewBox="0 0 32 32" fill="none" stroke="var(--blue)" stroke-width="1.2">
        <circle cx="16" cy="16" r="15"/>
        <circle cx="16" cy="16" r="6"/><circle cx="16" cy="16" r="2.5"/>
        <path d="M16 7v3M16 22v3M7 16h3M22 16h3M10 10l2 2M20 20l2 2M22 10l-2 2M10 22l2-2"/>
      </svg>
      Parking lot,<br>light repair
    </div>
    <div class="service">
      <svg width="32" height="32" viewBox="0 0 32 32" fill="none" stroke="var(--blue)" stroke-width="1.2">
        <circle cx="16" cy="16" r="15"/>
        <rect x="8" y="19" width="16" height="4"/>
        <path d="M12 19v-5h5l2 3M14 14v-3"/>
      </svg>
      Floor<br>repairing
    </div>
    <div class="service">
      <svg width="32" height="32" viewBox="0 0 32 32" fill="none" stroke="var(--blue)" stroke-width="1.2">
        <circle cx="16" cy="16" r="15"/>
        <rect x="11" y="9" width="7" height="9" rx="2" transform="rotate(-35 14 13)" fill="var(--blue)"/>
        <path d="M17 19l2 4M15 20l1 4M19 18l3 3"/>
      </svg>
      Light<br>plumbing
    </div>
  </div>
</section>

</body>
</html>
```